Quill Physical Therapy Website

I would need a clean modern website built to showcase my Physical therapy brand and services. I would need a simple but descriptive website that can ultimately connect my patients to my electronic medical portal so they may book an appointment..

```html
<!DOCTYPE html>
<html lang="en">
<head>
<meta charset="utf-8">
<title>Quill Physical Therapy &amp; Wellness</title>
<link href="https://fonts.googleapis.com/css2?family=Montserrat:wght@400;500;600;700;800&family=Open+Sans:wght@400;600&display=swap" rel="stylesheet">
<style>
:root{
  --teal:#13a39a;
  --teal-dark:#0e7f86;
  --green:#7cc242;
  --green-soft:#8ccb52;
  --navy:#1d4f6b;
  --ink:#333c44;
  --grey:#6b7479;
  --mint:#e3f1ef;
  --purple:#6b72c0;
  --white:#ffffff;
}
*{box-sizing:border-box;margin:0;padding:0}
html,body{width:1200px;height:3966px;overflow:hidden}
body{position:relative;font-family:"Open Sans",Arial,sans-serif;color:var(--ink);background:var(--white)}
.abs{position:absolute}
.head-font{font-family:"Montserrat",Arial,sans-serif}

/* header */
.site-header{position:absolute;left:0;top:0;width:1200px;height:110px;background:var(--white);z-index:5}
.brand{position:absolute;left:104px;top:28px;display:flex;align-items:center;gap:10px}
.brand-dot{width:50px;height:50px;border-radius:50%;border:4px solid var(--teal)}
.brand-name{font-family:"Montserrat",sans-serif;font-weight:800;font-size:38px;color:var(--teal);letter-spacing:1px}
.top-tab{position:absolute;left:585px;top:0;width:495px;height:44px;border-radius:0 0 40px 40px;background:linear-gradient(90deg,var(--green),var(--teal));display:flex;align-items:center;justify-content:center;gap:38px;font-family:"Montserrat",sans-serif;font-weight:600;font-size:13.5px;color:var(--white)}
.top-tab span{display:flex;align-items:center;gap:6px}
.main-nav{position:absolute;left:364px;top:68px;display:flex;gap:44px;font-family:"Montserrat",sans-serif;font-size:12.5px;font-weight:500;color:var(--ink)}
.main-nav a{text-decoration:none;color:inherit;position:relative;padding-bottom:26px}
.main-nav a.active{color:var(--teal)}
.main-nav a.active::after{content:"";position:absolute;left:0;right:0;bottom:0;height:3px;background:var(--green)}

/* hero */
.hero{position:absolute;left:0;top:110px;width:1200px;height:660px;overflow:hidden}
.hero-photo{position:absolute;inset:0;background:linear-gradient(120deg,#c9c6c3 0%,#e4e2e0 45%,#d7d2cd 70%,#a9a7a5 100%)}
.hero-curve{position:absolute;left:0;top:0}
.hero-ring{position:absolute;left:86px;top:86px;width:456px;height:456px;border-radius:50%;border:3px solid var(--teal-dark)}
.hero-circle{position:absolute;left:110px;top:104px;width:424px;height:424px;border-radius:50%;background:linear-gradient(160deg,rgba(124,194,66,.95),rgba(19,163,154,.92));color:var(--white);text-align:center;font-family:"Montserrat",sans-serif}
.hero-circle .welcome{margin-top:124px;font-size:21px;letter-spacing:3px;font-weight:400}
.hero-circle h1{font-size:40px;font-weight:700;margin-top:6px;line-height:1.05;letter-spacing:1px}
.hero-circle h1 small{display:block;font-size:27px;margin-top:6px}
.hero-btn{display:inline-block;margin-top:18px;background:var(--green);color:var(--white);font-weight:700;font-size:15px;letter-spacing:1px;padding:17px 38px;border-radius:30px}
.arrow{position:absolute;top:272px}

/* about */
.about{position:absolute;left:0;top:770px;width:1200px;height:568px;background:linear-gradient(120deg,var(--purple) 0%,#4e86b5 45%,#2f8f9a 100%);overflow:hidden}
.about-photo{position:absolute;left:64px;top:20px;width:508px;height:548px;background:linear-gradient(160deg,#e8e1da,#9aa6b2 60%,#3a5f86);border-radius:48% 48% 0 0/38% 38% 0 0}
.about-text{position:absolute;left:620px;top:116px;width:480px;color:var(--white)}
.eyebrow{font-family:"Montserrat",sans-serif;font-weight:600;font-size:15px;letter-spacing:3px}
.about-text h2{font-family:"Montserrat",sans-serif;font-size:36px;font-weight:400;letter-spacing:1px;margin-top:4px}
.about-text h2 b{font-weight:700}
.bar{width:100px;height:4px;background:var(--green);margin-top:10px}
.about-text p{font-size:13.5px;line-height:29px;margin-top:22px}
.outline-btn{display:inline-block;margin-top:24px;margin-left:-6px;border:2px solid var(--white);border-radius:30px;padding:14px 34px;font-family:"Montserrat",sans-serif;font-weight:600;font-size:13px;letter-spacing:1px;color:var(--white)}

/* services */
.services{position:absolute;left:0;top:1338px;width:1200px;height:610px}
.services-curve{position:absolute;left:0;top:0}
.section-title{text-align:center;font-family:"Montserrat",sans-serif}
.section-title .eyebrow{color:var(--navy);font-size:14.5px}
.section-title h2{font-size:33px;font-weight:400;color:var(--navy);letter-spacing:1.5px;margin-top:4px}
.section-title h2 b{font-weight:700}
.section-title .bar{margin:6px auto 0}
.svc{position:absolute;top:196px;width:348px;height:348px;border-radius:50%;overflow:hidden;color:var(--white);text-align:center;font-family:"Montserrat",sans-serif}
.svc h3{font-size:18px;font-weight:700;letter-spacing:.5px}
.svc p{font-family:"Open Sans",sans-serif;font-size:12.5px;line-height:20px;width:230px;margin:6px auto 0}
.svc .cap{position:absolute;left:0;right:0;bottom:44px}
.svc-one{left:103px;background:linear-gradient(180deg,#c9cfcf,#5f7170 55%,#2c3a3a)}
.svc-two{left:420px;background:radial-gradient(circle,#7fc34a,#5ea93c);z-index:2}
.svc-three{left:746px;background:linear-gradient(180deg,#d4a77f,#8a6a55 55%,#3a2f2f)}
.svc-two .cap{top:124px;bottom:auto}

/* panels */
.panel{position:absolute;top:1948px;height:496px;color:var(--white);text-align:center;font-family:"Montserrat",sans-serif}
.panel-left{left:0;width:603px;background:linear-gradient(160deg,#1cb0a4,#0fa09a);border-radius:0 60px 60px 0}
.panel-right{left:603px;width:597px;background:linear-gradient(160deg,#8ccd56,#78bf44);border-radius:60px 0 0 0}
.panel h2{margin-top:150px;font-size:29px;font-weight:400;letter-spacing:1.5px}
.panel h2 b{font-weight:700}
.panel .bar{background:var(--white);margin:4px auto 0;width:92px}
.panel p{font-family:"Open Sans",sans-serif;font-size:15px;line-height:24px;width:430px;margin:32px auto 0}
.pill{display:inline-block;margin-top:26px;background:var(--white);border-radius:30px;padding:14px 42px;font-weight:600;font-size:12.5px;letter-spacing:1px}
.panel-left .pill{color:var(--teal)}
.panel-right .pill{color:var(--teal)}

/* why */
.why{position:absolute;left:0;top:2444px;width:1200px;height:616px;background:linear-gradient(90deg,#ffffff 0%,#ffffff 45%,#f1f3f4 100%)}
.why-photo{position:absolute;left:600px;top:0;width:600px;height:616px;background:linear-gradient(120deg,#f1f2f3 0%,#dfe3e6 40%,#8a9aa6 70%,#2e3d4d 100%)}
.why-title{position:absolute;left:102px;top:100px;font-family:"Montserrat",sans-serif;font-size:29px;font-weight:400;letter-spacing:1px;color:var(--ink)}
.why-title b{color:var(--teal);font-weight:700}
.why .bar{position:absolute;left:104px;top:148px;width:96px}
.why-lead{position:absolute;left:104px;top:172px;width:480px;font-size:15px;line-height:23px;color:var(--ink)}
.feat{position:absolute;display:flex;gap:12px;width:260px}
.feat-icon{flex:none;width:74px;height:74px;border-radius:50%;background:linear-gradient(160deg,var(--teal),var(--green));display:flex;align-items:center;justify-content:center}
.feat h4{font-family:"Open Sans",sans-serif;font-size:16px;font-weight:600;color:var(--ink);margin-top:4px}
.feat p{font-size:10.5px;line-height:15px;color:var(--grey);margin-top:4px}

/* booking */
.booking{position:absolute;left:0;top:3060px;width:1200px;height:533px;background:var(--mint);overflow:hidden}
.booking .section-title{margin-top:80px}
.booking .eyebrow{color:var(--teal);font-weight:500;font-size:14.5px}
.booking h2{color:var(--navy)}
.field{position:absolute;background:var(--white);border:1px solid #d3dedd;font-family:"Montserrat",sans-serif;font-size:12px;font-weight:600;color:var(--ink);padding:20px;display:flex;align-items:flex-start;gap:8px}
.submit{position:absolute;left:498px;top:390px;width:250px;height:52px;border-radius:30px;background:var(--green);color:var(--white);font-family:"Montserrat",sans-serif;font-weight:600;font-size:15px;letter-spacing:1px;display:flex;align-items:center;justify-content:center}

/* footer */
.site-footer{position:absolute;left:0;top:3593px;width:1200px;height:312px;background:var(--teal);color:var(--white)}
.foot-brand{position:absolute;left:136px;top:80px;width:190px;text-align:center}
.foot-brand .dot{width:74px;height:74px;border-radius:50%;border:5px solid var(--white);margin:0 auto}
.foot-brand .name{font-family:"Montserrat",sans-serif;font-weight:800;font-size:44px;letter-spacing:1px;margin-top:18px}
.foot-brand .tag{font-family:"Montserrat",sans-serif;font-weight:700;font-size:10px;letter-spacing:.5px}
.divider{position:absolute;top:0;width:1px;height:312px;background:rgba(255,255,255,.35)}
.foot-col{position:absolute;top:78px}
.foot-col h5{font-family:"Montserrat",sans-serif;font-size:15px;font-weight:700;letter-spacing:.5px;border-left:3px solid var(--white);padding-left:38px;margin-left:-41px}
.foot-col ul{list-style:none;margin-top:12px}
.foot-col li{font-size:12px;line-height:28px}
.contact-line{display:flex;gap:10px;font-size:12px;line-height:23px}
.socials{display:flex;gap:7px;margin-top:16px}
.socials span{width:29px;height:29px;border-radius:50%;border:3px solid var(--white)}
.copyright{position:absolute;left:0;top:3905px;width:1200px;height:61px;background:var(--teal-dark);color:rgba(255,255,255,.85);font-size:11.5px;display:flex;align-items:center;justify-content:center}
</style>
</head>
<body>

<header class="site-header">
  <div class="brand"><span class="brand-dot"></span><span class="brand-name">QUILL</span></div>
  <div class="top-tab">
    <span><svg width="15" height="15" viewBox="0 0 16 16"><circle cx="8" cy="8" r="7" fill="#fff"/><path d="M4.5 8.2l2.3 2.3 4.7-4.7" stroke="#7cc242" stroke-width="2" fill="none"/></svg>BOOK APPOINTMENT</span>
    <span><svg width="16" height="16" viewBox="0 0 24 24"><path d="M6.6 10.8a15 15 0 006.6 6.6l2.2-2.2c.3-.3.7-.4 1-.2 1.1.4 2.3.6 3.6.6.6 0 1 .4 1 1V20c0 .6-.4 1-1 1A17 17 0 013 4c0-.6.4-1 1-1h3.5c.6 0 1 .4 1 1 0 1.3.2 2.5.6 3.6.1.3 0 .7-.2 1z" fill="#fff"/></svg>CALL US +123 555 0182</span>
  </div>
  <nav class="main-nav">
    <a class="active">HOME</a><a>ABOUT US</a><a>OUR SERVICES</a><a>WHY CHOOSE US</a><a>TESTIMONIALS</a><a>CONTACT US</a>
  </nav>
</header>

<section class="hero">
  <div class="hero-photo" role="img" aria-label="Photo of a therapist giving a back treatment to a patient lying on a table"></div>
  <svg class="hero-curve" width="1200" height="660" viewBox="0 0 1200 660">
    <defs><linearGradient id="heroG" x1="0" y1="0" x2="1" y2="1"><stop offset="0" stop-color="#4f86b6"/><stop offset="1" stop-color="#2a8e9a"/></linearGradient></defs>
    <path d="M1200 470 C1160 560 1090 630 1000 660 L1200 660 Z" fill="url(#heroG)"/>
  </svg>
  <div class="hero-ring"></div>
  <div class="hero-circle">
    <p class="welcome">WELCOME TO</p>
    <h1>QUILL PHYSICAL<small>THERAPY &amp; WELLNESS</small></h1>
    <span class="hero-btn">BOOK APPOINTMENT</span>
  </div>
  <svg class="arrow" style="left:26px" width="22" height="38" viewBox="0 0 22 38"><path d="M19 3L4 19l15 16" stroke="#fff" stroke-width="4" fill="none"/></svg>
  <svg class="arrow" style="left:1158px" width="22" height="38" viewBox="0 0 22 38"><path d="M3 3l15 16L3 35" stroke="#fff" stroke-width="4" fill="none"/></svg>
</section>

<section class="about">
  <div class="about-photo" role="img" aria-label="Photo of a physiotherapist assessing a woman's neck and shoulder"></div>
  <div class="about-text">
    <p class="eyebrow">WHO WE ARE</p>
    <h2>ABOUT <b>QUILL</b></h2>
    <div class="bar"></div>
    <p>Lorem Ipsum is simply dummy text of the printing and typesetting industry. Lorem Ipsum has been the industry's standard dummy text ever since the 1500s, when an unknown printer took a galley of type and scrambled it to make a type specimen book. It has survived not only five centuries, but also the leap into electronic typesetting, remaining essentially unchanged. Lorem Ipsum is simply dummy.</p>
    <span class="outline-btn">LEARN MORE</span>
  </div>
</section>

<section class="services">
  <svg class="services-curve" width="1200" height="160" viewBox="0 0 1200 160">
    <path d="M0 0 H200 C90 10 20 80 0 150 Z" fill="#4c7db6"/>
  </svg>
  <div class="section-title" style="position:absolute;left:0;width:1200px;top:84px">
    <p class="eyebrow">WHAT WE DO</p>
    <h2><b>SERVICES</b> PROVIDE</h2>
    <div class="bar"></div>
  </div>
  <div class="svc svc-one" role="img" aria-label="Photo of a therapist stretching a patient's leg">
    <div class="cap"><h3>PHYSICAL THERAPY</h3><p>Lorem ipsum dolor sit amet, consectetur adipiscing elit sed.</p></div>
  </div>
  <div class="svc svc-two" role="img" aria-label="Green tinted photo of a back treatment">
    <div class="cap"><h3>INJURY PAIN</h3><p>Lorem ipsum dolor sit amet, consectetur adipiscing elit sed.or sit amet-consectetur adipiscing.</p>
      <svg style="margin-top:12px" width="40" height="40" viewBox="0 0 40 40"><circle cx="20" cy="20" r="18" stroke="#fff" stroke-width="2" fill="none"/><path d="M13 17l7 7 7-7" stroke="#fff" stroke-width="2.5" fill="none"/></svg>
    </div>
  </div>
  <div class="svc svc-three" role="img" aria-label="Photo of a relaxing head massage with candles">
    <div class="cap"><h3>WELLNESS THERAPY</h3><p>Lorem ipsum dolor sit amet, consectetur adipiscing elit sed do.</p></div>
  </div>
</section>

<section class="panel panel-left" role="img" aria-label="Teal tinted photo of a physical therapy session">
  <h2><b>PHYSICAL</b> THERAPY</h2><div class="bar"></div>
  <p>Lorem Ipsum is simply dummy text of the printing and typesetting industry. Lorem Ipsum has been the industry's standard dummy text ever since</p>
  <span class="pill">LEARN MORE</span>
</section>
<section class="panel panel-right" role="img" aria-label="Green tinted photo of a relaxing massage">
  <h2><b>WELLNESS</b> THERAPY</h2><div class="bar"></div>
  <p>Lorem Ipsum is simply dummy text of the printing and typesetting industry. Lorem Ipsum has been the industry's standard dummy text ever since</p>
  <span class="pill">LEARN MORE</span>
</section>

<section class="why">
  <div class="why-photo" role="img" aria-label="Photo of a therapist stretching a patient's arm in a bright clinic"></div>
  <h2 class="why-title">WHY <b>CHOOSE QUILL</b></h2>
  <div class="bar"></div>
  <p class="why-lead">Lorem Ipsum is simply dummy text of the printing and typesetting industry. Lorem Ipsum has been the industry's standard dummy text ever sinceLorem Ipsum is simply dummy.</p>
  <div class="feat" style="left:98px;top:290px">
    <span class="feat-icon"><svg width="36" height="36" viewBox="0 0 36 36" fill="none" stroke="#fff" stroke-width="2"><circle cx="18" cy="12" r="5"/><path d="M8 30c0-6 4-10 10-10s10 4 10 10"/></svg></span>
    <div><h4>Therapy Specialist</h4><p>Donec convallis pede venenatis nibh Duis quam</p></div>
  </div>
  <div class="feat" style="left:355px;top:290px">
    <span class="feat-icon"><svg width="36" height="36" viewBox="0 0 36 36" fill="none" stroke="#fff" stroke-width="2"><path d="M18 30S5 22 5 13a6.5 6.5 0 0113-2 6.5 6.5 0 0113 2c0 9-13 17-13 17z"/></svg></span>
    <div><h4>Wellness Therapy</h4><p>Donec convallis pede venenatis nibh Duis quam</p></div>
  </div>
  <div class="feat" style="left:96px;top:408px">
    <span class="feat-icon"><svg width="36" height="36" viewBox="0 0 36 36" fill="none" stroke="#fff" stroke-width="2"><circle cx="18" cy="9" r="4"/><path d="M10 22h16M8 28h20M14 22v-6h8v6"/></svg></span>
    <div><h4>Injury Pain Relief</h4><p>Donec convallis pede venenatis nibh Duis quam</p></div>
  </div>
  <div class="feat" style="left:357px;top:408px">
    <span class="feat-icon"><svg width="36" height="36" viewBox="0 0 36 36" fill="none" stroke="#fff" stroke-width="2"><circle cx="18" cy="18" r="12"/><path d="M8 12c6 2 14 10 16 16M6 20c6-2 14-8 16-14"/></svg></span>
    <div><h4>Sports Therapy</h4><p>Donec convallis pede venenatis nibh Duis quam</p></div>
  </div>
</section>

<section class="booking">
  <svg class="abs" style="left:440px;top:0" width="340" height="200" viewBox="0 0 340 200"><circle cx="170" cy="170" r="150" stroke="#d6ebe7" stroke-width="22" fill="none"/></svg>
  <div class="section-title" style="position:relative">
    <p class="eyebrow">GET IN TOUCH</p>
    <h2>BOOK <b>APPOINTMENT</b></h2>
    <div class="bar"></div>
  </div>
  <div class="field" style="left:200px;top:182px;width:406px;height:50px">Name*</div>
  <div class="field" style="left:200px;top:244px;width:406px;height:50px">Email address*</div>
  <div class="field" style="left:200px;top:306px;width:200px;height:52px;align-items:center">
    <svg width="16" height="16" viewBox="0 0 16 16"><circle cx="8" cy="8" r="6.5" stroke="#7cc242" stroke-width="1.5" fill="none"/><path d="M8 4.5V8l2.5 1.5" stroke="#7cc242" stroke-width="1.5" fill="none"/></svg>Perfer Time</div>
  <div class="field" style="left:410px;top:306px;width:196px;height:52px;align-items:center">
    <svg width="17" height="16" viewBox="0 0 17 16"><rect x="1" y="2.5" width="15" height="12.5" rx="1" stroke="#7cc242" stroke-width="1.5" fill="none"/><path d="M1 6.5h15M5 1v3M12 1v3" stroke="#7cc242" stroke-width="1.5"/></svg>Select Date</div>
  <div class="field" style="left:618px;top:182px;width:406px;height:176px">Message</div>
  <div class="submit">BOOK APPOINTMENT</div>
</section>

<footer class="site-footer">
  <div class="foot-brand">
    <div class="dot"></div>
    <div class="name">QUILL</div>
    <div class="tag">PHYSICAL THERAPY &amp; WELLNESS</div>
  </div>
  <span class="divider" style="left:393px"></span>
  <span class="divider" style="left:601px"></span>
  <span class="divider" style="left:810px"></span>
  <div class="foot-col" style="left:435px">
    <h5>NAVIGATE</h5>
    <ul><li>Home</li><li>About Us</li><li>Our Services</li><li>New Products</li><li>Contact Us</li></ul>
  </div>
  <div class="foot-col" style="left:632px">
    <h5>RESOURCES</h5>
    <ul><li>News</li><li>Testimonials</li><li>Privacy Policy</li><li>Terms &amp; Condition</li></ul>
  </div>
  <div class="foot-col" style="left:849px">
    <h5 style="border-left:none;padding-left:0;margin-left:0">CONTACT US</h5>
    <div style="margin-top:12px">
      <div class="contact-line"><svg width="13" height="16" viewBox="0 0 13 16"><path d="M6.5 0A6 6 0 00.5 6c0 4.5 6 10 6 10s6-5.5 6-10a6 6 0 00-6-6zm0 8.3a2.3 2.3 0 110-4.6 2.3 2.3 0 010 4.6z" fill="#fff"/></svg><span>Office North | Linden Avenue 14<br>Office South | Harbor Road 9</span></div>
      <div class="contact-line"><svg width="13" height="16" viewBox="0 0 24 24"><path d="M6.6 10.8a15 15 0 006.6 6.6l2.2-2.2c.3-.3.7-.4 1-.2 1.1.4 2.3.6 3.6.6.6 0 1 .4 1 1V20c0 .6-.4 1-1 1A17 17 0 013 4c0-.6.4-1 1-1h3.5c.6 0 1 .4 1 1 0 1.3.2 2.5.6 3.6.1.3 0 .7-.2 1z" fill="#fff"/></svg><span>Tel: (1300) 555 2718</span></div>
      <div class="contact-line"><svg width="13" height="16" viewBox="0 0 13 16"><rect x="0" y="4" width="13" height="9" fill="#fff"/><path d="M0 4l6.5 5L13 4" stroke="#13a39a" stroke-width="1.2" fill="none"/></svg><span>Email: info@quillclinic.example</span></div>
    </div>
    <div class="socials"><span></span><span></span><span></span><span></span></div>
  </div>
</footer>
<div class="copyright">© 2021 Quill | All Rights Reserved &nbsp;|&nbsp; Terms &amp; Condition</div>

</body>
</html>
```